Harrow Grading LLC business card design

Excavation company business cards

Contact Information for Business Card

Harrow Grading LLC cell phone 208-417-6290 office phone 208-319-4856 harrowgradingllc@maplecove.com Driveways, site prep, retaining walls, septic systems, rock delivery

Colors

Designer to choose colors to be used in the design.

```html
<!DOCTYPE html>
<html lang="en">
<head>
<meta charset="utf-8">
<title>Harrow Grading LLC – Business Card</title>
<link href="https://fonts.googleapis.com/css2?family=Roboto:ital,wght@0,400;0,500;0,700;0,900;1,400&display=swap" rel="stylesheet">
<style>
  :root {
    --backdrop: #2b2b2b;
    --card-grey: #666666;
    --card-white: #ffffff;
    --orange: #ec6c22;
    --ink: #1f1f1f;
    --rule-grey: #6a6a6a;
    --text-light: #ffffff;
  }
  * { margin: 0; padding: 0; box-sizing: border-box; }
  html, body {
    width: 1200px; height: 900px; overflow: hidden;
    background: var(--backdrop);
    font-family: "Roboto", Arial, sans-serif;
  }
  .stage {
    width: 1200px; height: 900px;
    display: flex; flex-direction: column; align-items: center; justify-content: center;
    gap: 30px;
  }
  .card {
    position: relative;
    width: 720px; height: 411px;
    overflow: hidden;
    box-shadow: 0 10px 28px rgba(0,0,0,0.45);
  }

  /* Back side */
  .card-back { background: var(--card-grey); }
  .card-back .wordmark {
    position: absolute; left: 0; right: 0; top: 130px;
    display: flex; align-items: center; justify-content: center; gap: 14px;
  }
  .wordmark-dot {
    width: 22px; height: 22px; border-radius: 50%; background: var(--orange);
  }
  .wordmark-name {
    font-weight: 900; font-size: 46px; color: var(--orange);
    text-transform: uppercase; letter-spacing: 1px;
  }
  .services {
    position: absolute; left: 0; right: 0; bottom: 56px;
    text-align: center; color: var(--text-light);
    font-size: 19px; letter-spacing: 0.5px;
  }
  .services .sep { color: var(--orange); margin: 0 8px; }

  /* Front side */
  .card-front { background: var(--card-white); }
  .card-front .wordmark {
    position: absolute; left: 34px; top: 150px; width: 300px;
    display: flex; align-items: center; gap: 10px;
  }
  .card-front .wordmark-name { font-size: 30px; line-height: 1.05; }
  .card-front .wordmark-dot { width: 16px; height: 16px; flex: none; }
  .divider {
    position: absolute; left: 352px; top: 105px;
    width: 2px; height: 190px; background: var(--rule-grey);
  }
  .person { position: absolute; left: 384px; top: 104px; }
  .person-name {
    font-weight: 700; font-size: 32px; color: var(--orange);
    text-transform: uppercase; letter-spacing: 0.5px;
  }
  .person-title { font-size: 21px; color: var(--ink); margin-top: 2px; }
  .contact-list {
    position: absolute; left: 384px; top: 196px;
    list-style: none; color: var(--ink); font-size: 19px;
  }
  .contact-list li { display: flex; align-items: center; gap: 9px; height: 29px; }
  .contact-list svg { width: 16px; height: 16px; flex: none; }
  .band { position: absolute; left: 0; bottom: 0; width: 720px; height: 80px; }
</style>
</head>
<body>
<main class="stage">

  <section class="card card-back" aria-label="Card back">
    <div class="wordmark">
      <span class="wordmark-dot"></span>
      <span class="wordmark-name">Harrow Grading LLC</span>
    </div>
    <p class="services">
      Driveways<span class="sep">•</span>Site Prep<span class="sep">•</span>Retaining Walls<span class="sep">•</span>Septic Systems<span class="sep">•</span>Rock Delivery
    </p>
  </section>

  <section class="card card-front" aria-label="Card front">
    <div class="wordmark">
      <span class="wordmark-dot"></span>
      <span class="wordmark-name">Harrow Grading LLC</span>
    </div>

    <div class="divider"></div>

    <div class="person">
      <p class="person-name">Dalen Brooks</p>
      <p class="person-title">Founder</p>
    </div>

    <ul class="contact-list">
      <li>
        <svg viewBox="0 0 16 16" aria-hidden="true"><path fill="var(--orange)" d="M3.6 1.5l2.3 2.4-1.3 1.9c.9 2 2.6 3.8 4.6 4.7l1.9-1.3 2.4 2.3-1.4 2.5C6.6 13.7 2.3 9.4 1.1 2.9z"/></svg>
        <span>208-319-4856</span>
      </li>
      <li>
        <svg viewBox="0 0 16 16" aria-hidden="true"><rect x="4" y="1" width="8" height="14" rx="1.5" fill="none" stroke="var(--orange)" stroke-width="1.6"/><circle cx="8" cy="12.3" r="0.9" fill="var(--orange)"/></svg>
        <span>208-417-6290</span>
      </li>
      <li>
        <svg viewBox="0 0 16 16" aria-hidden="true"><rect x="1" y="3" width="14" height="10" fill="var(--orange)"/><path d="M1 3l7 6 7-6" fill="none" stroke="#fff" stroke-width="1.3"/></svg>
        <span>harrowgradingllc@maplecove.com</span>
      </li>
      <li>
        <svg viewBox="0 0 16 16" aria-hidden="true"><circle cx="8" cy="8" r="7" fill="var(--orange)"/><path d="M1 8h14M8 1c-3 3.5-3 10.5 0 14M8 1c3 3.5 3 10.5 0 14" fill="none" stroke="#fff" stroke-width="1"/></svg>
        <span>www.harrowgradingco.com</span>
      </li>
    </ul>

    <svg class="band" viewBox="0 0 720 80" aria-hidden="true">
      <rect x="0" y="34" width="400" height="4" fill="var(--rule-grey)"/>
      <path d="M0 50 H370 C385 50 385 34 405 34 H720 V80 H0 Z" fill="var(--orange)"/>
    </svg>
  </section>

</main>
</body>
</html>
```